Young, modern, highly skilled carpenter needs business card design

I need a business card design for my construction business. Its called 'Barlow Construction Services'. Im looking for a ultra modern design that incorporates B C S, the first letters of the name with only a subtle reference to carpentry. The design should reflect my high quality work and eye for detail. i have also uploaded some exmaple designs i like.

Industry/Entity Type

Construction

Requirements
Must have
• Name of business, my name, mobile number, ABN number, email address
Nice to have
• A logo incorporating the name of the business

```html
<!DOCTYPE html>
<html lang="en">
<head>
<meta charset="utf-8">
<title>Barlow Construction Services – Business Card</title>
<link rel="stylesheet" href="https://fonts.googleapis.com/css2?family=Cabin:wght@400;600&display=swap">
<style>
  :root {
    --backdrop: #7d8e8d;
    --card: #ffffff;
    --ink: #3b3f3a;
    --accent: #f5cc17;
  }
  * { margin: 0; padding: 0; box-sizing: border-box; }
  html, body {
    width: 1200px;
    height: 900px;
    overflow: hidden;
  }
  body {
    background: var(--backdrop);
    font-family: "Cabin", sans-serif;
    color: var(--ink);
    position: relative;
  }
  .card {
    position: absolute;
    left: 335px;
    width: 545px;
    background: var(--card);
  }
  .card--front { top: 60px; height: 370px; }
  .card--back  { top: 460px; height: 376px; }

  .wordmark {
    position: absolute;
    display: flex;
    align-items: center;
    gap: 10px;
  }
  .wordmark__square {
    width: 14px;
    height: 14px;
    background: var(--accent);
    flex: none;
  }
  .card--front .wordmark {
    left: 67px;
    top: 295px;
  }
  .card--front .wordmark__name {
    font-size: 21px;
    font-weight: 400;
    letter-spacing: 0.2px;
    color: var(--ink);
  }

  .contact {
    position: absolute;
    left: 70px;
    top: 50px;
    font-size: 19px;
    line-height: 27px;
  }
  .contact__name {
    color: var(--accent);
    font-weight: 600;
  }
  .contact__divider { color: var(--accent); }

  .card--back .wordmark {
    right: 56px;
    bottom: 52px;
  }
  .card--back .wordmark__name {
    font-size: 34px;
    font-weight: 600;
    letter-spacing: 2px;
    color: var(--ink);
  }
</style>
</head>
<body>
  <section class="card card--front" aria-label="Business card front">
    <div class="wordmark">
      <span class="wordmark__square"></span>
      <span class="wordmark__name">Barlow Construction Services</span>
    </div>
  </section>

  <section class="card card--back" aria-label="Business card back">
    <div class="contact">
      <p class="contact__name">Liam Barlow</p>
      <p class="contact__email">liam_barlow@mailbox.com</p>
      <p class="contact__line">0412 385620 <span class="contact__divider">//</span> ABN 51 824 753 556</p>
    </div>
    <div class="wordmark">
      <span class="wordmark__square"></span>
      <span class="wordmark__name">BCS</span>
    </div>
  </section>
</body>
</html>
```